Oral Surgeon Referral Pads

Hello. We need referral pads for Dr Elsabet Quorvane, DDS board certified oral surgeon's new office - Harrowgate Dunmere Oral & Maxillofacial Surgery. See logo uploaded. See some images we would like included
Updates

Designs look the same

Font styles to use
Serif
Script

Colors
00AB8E
00BBA5
67D7C9
C6EFE9
E9F9F6

Requirements
Must have
• Color Pantone 623c. Also foldable business cards

```html
<!DOCTYPE html>
<html lang="en">
<head>
<meta charset="utf-8">
<title>Harrowgate Dunmere Oral &amp; Maxillofacial Surgery – Stationery</title>
<link rel="stylesheet" href="https://fonts.googleapis.com/css2?family=Tinos:wght@400;700&display=swap">
<style>
  :root {
    --stage: #232324;
    --paper: #ffffff;
    --sage: #9dbcb1;
    --sage-text: #8db3a6;
    --ink: #6a6a6a;
    --rule: #5a5a5a;
    --ghost: #f1f1f1;
  }
  * { margin: 0; padding: 0; box-sizing: border-box; }
  html, body { width: 1200px; height: 1200px; overflow: hidden; }
  body {
    position: relative;
    background: var(--stage);
    font-family: "Tinos", "Times New Roman", serif;
    color: var(--ink);
  }
  .sheet, .card {
    position: absolute;
    background: var(--paper);
    overflow: hidden;
  }

  /* ---------- brand block (shared) ---------- */
  .brand { position: absolute; left: 0; right: 0; text-align: center; }
  .brand-dot {
    display: block; margin: 0 auto;
    border: 2px solid var(--sage); border-radius: 50%;
  }
  .brand-name {
    display: block; color: var(--sage-text); font-weight: 400; line-height: 1;
  }
  .brand-band {
    position: absolute; left: 0; right: 0;
    display: flex; align-items: center;
  }
  .brand-band .bar { flex: 1; background: var(--sage); }
  .brand-band .sub {
    color: var(--sage-text); font-weight: 400; padding: 0 6px; white-space: nowrap; line-height: 1;
  }
  .brand-rule { position: absolute; left: 0; right: 0; background: var(--rule); }

  /* ---------- letterhead ---------- */
  .sheet { left: 122px; top: 70px; width: 517px; height: 731px; }
  .sheet .brand { top: 18px; }
  .sheet .brand-dot { width: 30px; height: 30px; }
  .sheet .brand-name { font-size: 16px; margin-top: 10px; }
  .sheet .brand-band { top: 84px; height: 12px; }
  .sheet .brand-band .bar { height: 6px; }
  .sheet .brand-band .sub { font-size: 8.5px; }
  .sheet .brand-rule { top: 96px; height: 1.5px; }

  .sheet-contacts {
    position: absolute; left: 27px; top: 29px; list-style: none;
    font-size: 7.5px; line-height: 12.3px;
  }
  .sheet-contacts li { display: flex; align-items: center; gap: 4px; }
  .sheet-address {
    position: absolute; right: 27px; top: 16px; text-align: right;
    font-size: 7.5px; line-height: 10.6px; font-style: normal; color: var(--ink);
  }
  .sheet-address .gap { display: block; height: 3px; }
  .sheet-ghost {
    position: absolute; left: 100px; top: 190px; width: 380px; height: 380px;
    border: 14px solid var(--ghost); border-radius: 50%;
  }

  /* ---------- business cards ---------- */
  .card { width: 372px; height: 212px; }
  .card .brand { top: 16px; }
  .card .brand-dot { width: 34px; height: 34px; }
  .card .brand-name { font-size: 18px; margin-top: 9px; }
  .card .brand-band { top: 85px; height: 12px; }
  .card .brand-band .bar { height: 7px; }
  .card .brand-band .sub { font-size: 9.5px; }
  .card .brand-rule { top: 100px; height: 1.5px; }

  .person {
    position: absolute; right: 196px; top: 130px; text-align: right;
    font-size: 9px; line-height: 11px;
  }
  .person-name { color: var(--sage-text); font-weight: 700; font-size: 12.5px; line-height: 15px; }
  .divider { position: absolute; left: 185px; top: 128px; width: 1px; height: 40px; background: #9a9a9a; }
  .contacts {
    position: absolute; left: 194px; top: 127px; list-style: none;
    font-size: 9px; line-height: 13.5px;
  }
  .contacts li { display: flex; align-items: center; gap: 4px; }
  .card-address {
    position: absolute; left: 0; right: 0; top: 184px; text-align: center; font-size: 9px;
  }
  .icon { width: 7px; height: 7px; flex: none; }
  .card .icon { width: 8px; height: 8px; }

  .card-exec-assistant { left: 710px; top: 68px; }
  .card-cfo            { left: 710px; top: 346px; }
  .card-assistant      { left: 710px; top: 619px; }
  .card-coordinator    { left: 118px; top: 920px; }
  .card-surgeon        { left: 706px; top: 920px; }
</style>
</head>
<body>

<svg width="0" height="0" style="position:absolute" aria-hidden="true">
  <defs>
    <symbol id="i-phone" viewBox="0 0 10 10">
      <path d="M2.2 1.2 L3.6 1 L4.3 3 L3.3 3.8 Q4.2 5.8 6.2 6.7 L7 5.7 L9 6.4 L8.8 7.8 Q8 9 6.6 8.8 Q2.6 7.8 1.2 3.4 Q1 2 2.2 1.2 Z" fill="none" stroke="#8a8a8a" stroke-width="0.9"/>
    </symbol>
    <symbol id="i-fax" viewBox="0 0 10 10">
      <rect x="1" y="4" width="8" height="4.5" rx="0.8" fill="none" stroke="#8a8a8a" stroke-width="0.9"/>
      <rect x="2.8" y="1.2" width="4.4" height="3" fill="none" stroke="#8a8a8a" stroke-width="0.9"/>
    </symbol>
    <symbol id="i-mail" viewBox="0 0 10 10">
      <rect x="1" y="2.2" width="8" height="5.8" fill="none" stroke="#8a8a8a" stroke-width="0.9"/>
      <path d="M1 2.4 L5 5.6 L9 2.4" fill="none" stroke="#8a8a8a" stroke-width="0.9"/>
    </symbol>
    <symbol id="i-web" viewBox="0 0 10 10">
      <circle cx="5" cy="5" r="4" fill="none" stroke="#8a8a8a" stroke-width="0.9"/>
      <ellipse cx="5" cy="5" rx="1.7" ry="4" fill="none" stroke="#8a8a8a" stroke-width="0.7"/>
      <path d="M1 5 H9" stroke="#8a8a8a" stroke-width="0.7"/>
    </symbol>
  </defs>
</svg>

<!-- Letterhead -->
<section class="sheet" aria-label="Letterhead">
  <ul class="sheet-contacts">
    <li><svg class="icon"><use href="#i-phone"/></svg>555-014-2286</li>
    <li><svg class="icon"><use href="#i-fax"/></svg>555-014-2280</li>
    <li><svg class="icon"><use href="#i-mail"/></svg>info@hdoms-clinic.com</li>
    <li><svg class="icon"><use href="#i-web"/></svg>www.hdoms-clinic.com</li>
  </ul>

  <div class="brand">
    <span class="brand-dot"></span>
    <span class="brand-name">Harrowgate Dunmere</span>
  </div>
  <div class="brand-band"><span class="bar"></span><span class="sub">Oral &amp; Maxillofacial Surgery</span><span class="bar"></span></div>
  <div class="brand-rule"></div>

  <address class="sheet-address">
    Harrowgate Dunmere Oral and Maxillofacial Surgery<br>
    Dr Elsabet Quorvane<span class="gap"></span>
    88 Linden Row<br>
    Suite 210<br>
    Harrowgate, NV<br>
    89021
  </address>

  <div class="sheet-ghost"></div>
</section>

<!-- Business cards -->
<section class="card card-exec-assistant" aria-label="Business card – Ilsa">
  <div class="brand"><span class="brand-dot"></span><span class="brand-name">Harrowgate Dunmere</span></div>
  <div class="brand-band"><span class="bar"></span><span class="sub">Oral &amp; Maxillofacial Surgery</span><span class="bar"></span></div>
  <div class="brand-rule"></div>
  <div class="person"><div class="person-name">Ilsa</div>Executive Surgical Assistant</div>
  <div class="divider"></div>
  <ul class="contacts">
    <li><svg class="icon"><use href="#i-phone"/></svg>555-014-2286</li>
    <li><svg class="icon"><use href="#i-mail"/></svg>Ilsa@hdoms-clinic.com</li>
    <li><svg class="icon"><use href="#i-web"/></svg>www.hdoms-clinic.com</li>
  </ul>
  <p class="card-address">88 Linden Row, Suite 210, Harrowgate, NV 89021</p>
</section>

<section class="card card-cfo" aria-label="Business card – Theo Quorvane">
  <div class="brand"><span class="brand-dot"></span><span class="brand-name">Harrowgate Dunmere</span></div>
  <div class="brand-band"><span class="bar"></span><span class="sub">Oral &amp; Maxillofacial Surgery</span><span class="bar"></span></div>
  <div class="brand-rule"></div>
  <div class="person"><div class="person-name">Theo Quorvane</div>CFO</div>
  <div class="divider"></div>
  <ul class="contacts">
    <li><svg class="icon"><use href="#i-phone"/></svg>555-014-2286</li>
    <li><svg class="icon"><use href="#i-mail"/></svg>theo@qvcap-group.com</li>
    <li><svg class="icon"><use href="#i-web"/></svg>www.hdoms-clinic.com</li>
  </ul>
  <p class="card-address">88 Linden Row, Suite 210, Harrowgate, NV 89021</p>
</section>

<section class="card card-assistant" aria-label="Business card – Mireth">
  <div class="brand"><span class="brand-dot"></span><span class="brand-name">Harrowgate Dunmere</span></div>
  <div class="brand-band"><span class="bar"></span><span class="sub">Oral &amp; Maxillofacial Surgery</span><span class="bar"></span></div>
  <div class="brand-rule"></div>
  <div class="person"><div class="person-name">Mireth</div>Surgical Assistant</div>
  <div class="divider"></div>
  <ul class="contacts">
    <li><svg class="icon"><use href="#i-phone"/></svg>555-014-2286</li>
    <li><svg class="icon"><use href="#i-mail"/></svg>Mireth@hdoms-clinic.com</li>
    <li><svg class="icon"><use href="#i-web"/></svg>www.hdoms-clinic.com</li>
  </ul>
  <p class="card-address">88 Linden Row, Suite 210, Harrowgate, NV 89021</p>
</section>

<section class="card card-coordinator" aria-label="Business card – Dorra">
  <div class="brand"><span class="brand-dot"></span><span class="brand-name">Harrowgate Dunmere</span></div>
  <div class="brand-band"><span class="bar"></span><span class="sub">Oral &amp; Maxillofacial Surgery</span><span class="bar"></span></div>
  <div class="brand-rule"></div>
  <div class="person"><div class="person-name">Dorra</div>Executive Office Coordinator</div>
  <div class="divider"></div>
  <ul class="contacts">
    <li><svg class="icon"><use href="#i-phone"/></svg>555-014-2286</li>
    <li><svg class="icon"><use href="#i-mail"/></svg>Dorra@hdoms-clinic.com</li>
    <li><svg class="icon"><use href="#i-web"/></svg>www.hdoms-clinic.com</li>
  </ul>
  <p class="card-address">88 Linden Row, Suite 210, Harrowgate, NV 89021</p>
</section>

<section class="card card-surgeon" aria-label="Business card – Elsabet Quorvane, DDS">
  <div class="brand"><span class="brand-dot"></span><span class="brand-name">Harrowgate Dunmere</span></div>
  <div class="brand-band"><span class="bar"></span><span class="sub">Oral &amp; Maxillofacial Surgery</span><span class="bar"></span></div>
  <div class="brand-rule"></div>
  <div class="person"><div class="person-name">Elsabet Quorvane, DDS</div>Board Certified Oral<br>and Maxillofacial Surgeon</div>
  <div class="divider"></div>
  <ul class="contacts">
    <li><svg class="icon"><use href="#i-phone"/></svg>555-017-6618</li>
    <li><svg class="icon"><use href="#i-mail"/></svg>Dr.Quorvane@hdoms-clinic.com</li>
    <li><svg class="icon"><use href="#i-web"/></svg>www.hdoms-clinic.com</li>
  </ul>
  <p class="card-address">88 Linden Row, Suite 210, Harrowgate, NV 89021</p>
</section>

</body>
</html>
```